Fern Moss Cleaning Tablets needs 4 x labels

We're about to launch a very exciting cleaning product to market and need your help to brand the 4 x bottles. www.fernmossly.com.au will change the way people buy and use household cleaning products whilst significantly reducing the impact on the earth.

The tablets are dropped into the long life recycled plastic bottle, you simply add water, wait for the tab to dissolve and begin cleaning.

Target Market(s)

Women aged between 30 - 65, care for the environment, want to use less plastic, are early adopters and like to try new things. Care about a clean home and using less chemicals. Want less packaging, less plastic, less carbon emissions.

Industry/Entity Type

House Cleaning

Font styles to use
Sans Serif

Requirements
Must have
• Each label must have an obvious colour differentiator and each label must be identical in it's dimensions and information. Should look uniform when all 4 bottles are aligned in the cupboard. Limited / no images apart from logo.
Nice to have
• Simple, clear, bold, striking. Limited / no pictures. Clean lines with lots of space.
Should not have
• Sparkwell Pane Label must have a strip of blue (hex BAE1FF).
Grime Hauler Kitchen Cleaner must have a strip of colour (FFD6F3)
The Fizzer Bathroom cleaner must have a colour strip hex # FFFFBA
The Allrounder Multip Purpose must have a strip of colour Hex #BAFFC9

```html
<!DOCTYPE html>
<html lang="en">
<head>
<meta charset="utf-8">
<title>Fern Moss – Grime Hauler Kitchen Cleaner Label</title>
<link rel="stylesheet" href="https://fonts.googleapis.com/css2?family=Archivo+Black&family=Big+Shoulders+Display:wght@700;800;900&family=Didact+Gothic&display=swap">
<style>
  :root {
    --paper-top: #fffdfd;
    --paper-bottom: #f8d6e6;
    --outline: #111111;
    --brand-teal: #134f5c;
    --product-pink: #d49bbc;
    --ink: #000000;
  }
  html, body {
    margin: 0;
    padding: 0;
    width: 1200px;
    height: 923px;
    overflow: hidden;
    background: #ffffff;
  }
  .label {
    position: relative;
    box-sizing: border-box;
    width: 1200px;
    height: 923px;
    border: 2px solid var(--outline);
    border-radius: 56px;
    background: linear-gradient(to bottom, var(--paper-top) 0%, #fae6ef 35%, var(--paper-bottom) 100%);
    overflow: hidden;
  }
  .line {
    position: absolute;
    left: 0;
    right: 0;
    margin: 0;
    text-align: center;
    white-space: nowrap;
  }
  .brand {
    top: 92px;
    display: flex;
    justify-content: center;
    align-items: center;
    gap: 16px;
  }
  .brand-dot {
    width: 34px;
    height: 34px;
    border-radius: 50%;
    background: var(--brand-teal);
  }
  .brand-name {
    font-family: "Big Shoulders Display", sans-serif;
    font-weight: 800;
    font-size: 112px;
    line-height: 1;
    color: var(--brand-teal);
    letter-spacing: 1px;
  }
  .product-name {
    top: 282px;
    left: 0;
    font-family: "Didact Gothic", sans-serif;
    font-size: 136px;
    line-height: 1;
    color: var(--product-pink);
    letter-spacing: 1px;
  }
  .product-type {
    top: 462px;
    left: 0;
    font-family: "Big Shoulders Display", sans-serif;
    font-weight: 900;
    font-size: 156px;
    line-height: 1;
    color: var(--ink);
    letter-spacing: 3px;
  }
  .tagline {
    top: 696px;
    left: 0;
    font-family: "Didact Gothic", sans-serif;
    font-size: 34px;
    line-height: 1;
    color: var(--ink);
    word-spacing: 10px;
  }
  .volume {
    top: 766px;
    left: 0;
    font-family: "Archivo Black", sans-serif;
    font-size: 42px;
    line-height: 1;
    color: var(--ink);
  }
  .origin {
    top: 836px;
    left: 0;
    font-family: "Big Shoulders Display", sans-serif;
    font-weight: 800;
    font-size: 38px;
    line-height: 1;
    color: var(--ink);
    word-spacing: 8px;
  }
</style>
</head>
<body>
  <main class="label">
    <div class="line brand">
      <span class="brand-name">Fern Moss</span>
      <span class="brand-dot"></span>
    </div>
    <h1 class="line product-name">Grime Hauler</h1>
    <h2 class="line product-type">Kitchen Cleaner</h2>
    <p class="line tagline">One Bottle. One Tab. Dissolve. Clean. Repeat.</p>
    <p class="line volume">500 ml</p>
    <p class="line origin">Kelpie Bay. Australia</p>
  </main>
</body>
</html>
```